Non fiction leadership Book Cover design needed for “Stay Bold: Build On Lasting Discipline”

I need a front cover design for a new book 6 X 9 traditional non-fiction book.

Title: "Stay BOLD - Build On Lasting Discipline"

The subtitle is not finalized- so use 2 lines of smaller dummy text

My brand guide is attached (please use the tan color sparingly)

I'd like to see BOLD look like it is in motion and "flying" across the page

Need CREATIVE designs and options

Do not want my picture on the front cover - I do want it on the back cover.

On the front cover I’d like to see creative use of font to create movement on “BOLD”

Target Market(s)

Business leaders

Industry/Entity Type

Aviation

Font styles to use
Other font styles liked:
• See style guide- can add additional font (modern script or san serif)

Colors
0054AA
0677BA
7BADD7
CADEEF
E8F1F8
EB3D1F
EC4F4E
F09395
F8D3D4
FCEDEE

Requirements
Must have
• Creative font use, using perspective to create movement/motion on BOLD
Should not have
• My picture on the front cover- my picture should be on the back cover

```html
<!DOCTYPE html>
<html lang="en">
<head>
<meta charset="utf-8">
<title>Stay Bold: Build On Lasting Discipline — Front Cover</title>
<link rel="stylesheet" href="https://fonts.googleapis.com/css2?family=Bebas+Neue&family=Great+Vibes&family=Montserrat:wght@500;700;900&display=swap">
<style>
  :root {
    --page-bg: #eef1f5;
    --sky-top: #050b1a;
    --sky-mid: #0b2a5c;
    --sky-low: #0560a3;
    --sky-base: #2c7bbb;
    --ink-white: #ffffff;
    --gold-light: #fbf0d2;
    --gold-mid: #ecc670;
    --gold-deep: #c99436;
    --trail: rgba(220, 230, 245, 0.55);
  }
  * { margin: 0; padding: 0; box-sizing: border-box; }
  html, body {
    width: 1200px;
    height: 675px;
    overflow: hidden;
    background: var(--page-bg);
  }
  .stage {
    width: 1200px;
    height: 675px;
    display: flex;
    justify-content: center;
    align-items: center;
  }
  .book-cover {
    width: 450px;
    height: 675px;
    display: block;
  }
  .tagline {
    font-family: "Montserrat", sans-serif;
    font-weight: 500;
    font-size: 13px;
    letter-spacing: 0.4px;
    fill: var(--ink-white);
  }
  .title-lead,
  .subtitle {
    font-family: "Bebas Neue", "Oswald", sans-serif;
    fill: var(--ink-white);
  }
  .title-lead { font-size: 92px; }
  .subtitle { font-size: 46px; }
  .title-script {
    font-family: "Great Vibes", cursive;
    font-size: 200px;
  }
  .author-first {
    font-family: "Montserrat", sans-serif;
    font-weight: 900;
    font-size: 47px;
    letter-spacing: 0.5px;
  }
  .author-last {
    font-family: "Montserrat", sans-serif;
    font-weight: 700;
    font-size: 20px;
    letter-spacing: 7px;
    fill: var(--ink-white);
  }
</style>
</head>
<body>
<main class="stage">
  <svg class="book-cover" viewBox="0 0 450 675" xmlns="http://www.w3.org/2000/svg" aria-labelledby="cover-title">
    <title id="cover-title">Stay Bold: Build On Lasting Discipline by Katherine Hawthorne</title>
    <defs>
      <linearGradient id="sky" x1="0" y1="0" x2="0" y2="1">
        <stop offset="0" stop-color="var(--sky-top)"/>
        <stop offset="0.35" stop-color="var(--sky-mid)"/>
        <stop offset="0.8" stop-color="var(--sky-low)"/>
        <stop offset="1" stop-color="var(--sky-base)"/>
      </linearGradient>
      <linearGradient id="gold" x1="0" y1="0" x2="0" y2="1">
        <stop offset="0" stop-color="var(--gold-light)"/>
        <stop offset="0.55" stop-color="var(--gold-mid)"/>
        <stop offset="1" stop-color="var(--gold-deep)"/>
      </linearGradient>
      <linearGradient id="contrail" x1="1" y1="0" x2="0" y2="1">
        <stop offset="0" stop-color="var(--trail)"/>
        <stop offset="1" stop-color="rgba(220,230,245,0)"/>
      </linearGradient>
    </defs>

    <rect class="cover-sky" width="450" height="675" fill="url(#sky)"/>

    <text class="tagline" x="225" y="55" text-anchor="middle">DISCIPLINE TODAY BUILDS THE LEADER YOU WILL</text>
    <text class="tagline" x="225" y="71" text-anchor="middle">BECOME TOMORROW, ONE STEADY CHOICE AT A TIME.</text>

    <!-- contrail and aircraft -->
    <path class="contrail" d="M352 168 C 300 210, 210 270, 130 312" stroke="url(#contrail)" stroke-width="6" fill="none" stroke-linecap="round"/>
    <g class="plane-icon" transform="translate(366 156) rotate(-40)" fill="var(--ink-white)">
      <path d="M-16 -2 L16 -2 Q20 0 16 2 L-16 2 Z"/>
      <path d="M2 -2 L-6 -16 L-2 -16 L8 -2 Z"/>
      <path d="M2 2 L-6 16 L-2 16 L8 2 Z"/>
      <path d="M-14 -2 L-18 -8 L-15 -8 L-10 -2 Z"/>
      <path d="M-14 2 L-18 8 L-15 8 L-10 2 Z"/>
    </g>

    <text class="title-lead" x="220" y="186" text-anchor="middle">STAY</text>

    <!-- motion swash -->
    <path class="speed-swash" d="M46 236 C 120 205, 280 192, 372 200 Q 382 204 372 207 C 280 204, 130 215, 52 240 Q 40 244 46 236 Z" fill="url(#gold)"/>

    <text class="title-script" x="232" y="410" text-anchor="middle" fill="url(#gold)" transform="rotate(-9 232 360) skewX(-8)">Bold</text>

    <text class="subtitle" x="212" y="466" text-anchor="middle">BUILD ON LASTING</text>
    <text class="subtitle" x="212" y="508" text-anchor="middle">DISCIPLINE</text>

    <text class="author-first" x="225" y="626" text-anchor="middle" fill="url(#gold)">KATHERINE</text>
    <text class="author-last" x="228" y="652" text-anchor="middle">HAWTHORNE</text>
  </svg>
</main>
</body>
</html>
```